Weightloss company needs Business Card

We want a business card that is clean and professional, yet portrays that we are a friendly, innovative, and versatile program designed to fit the needs of our clients.
I would like there to be 2 sides, one side having an appointment card, and the other side containing the logo and business information. There can be decorations on both sides. The logo is attached.

Target Market(s)

Men and women 40-60

Industry/Entity Type

Business

Contact Information for Business Card

Font styles to use
Sans Serif

Requirements
Must have
• The logo, space for business information
Nice to have
• The colors in the logo
Should not have
• No pictures of people or food

```html
<!DOCTYPE html>
<html lang="en">
<head>
<meta charset="utf-8">
<title>Brightturn Wellness – Business Card</title>
<link rel="stylesheet" href="https://fonts.googleapis.com/css2?family=Open+Sans:wght@400;600;700&display=swap">
<style>
  :root {
    --stage: #3a3431;
    --card-dark: #0d0d0d;
    --card-light: #ffffff;
    --brand-red: #e8173f;
    --text-light: #f2f2f2;
    --rule-dark: #5a1020;
    --dots: #333333;
  }
  * { box-sizing: border-box; margin: 0; padding: 0; }
  html, body {
    width: 1200px; height: 900px; overflow: hidden;
    background: var(--stage);
    font-family: "Open Sans", sans-serif;
  }
  .stage {
    width: 1200px; height: 900px;
    display: flex; align-items: center; justify-content: center; gap: 40px;
  }
  .card {
    width: 540px; height: 310px; position: relative;
    box-shadow: 0 12px 30px rgba(0,0,0,.45);
  }
  .card--front { background: var(--card-dark); color: var(--text-light); }
  .card--back { background: var(--card-light); color: var(--brand-red); }

  .brand {
    display: flex; align-items: center; gap: 10px;
    color: var(--brand-red); font-weight: 700; font-size: 26px; letter-spacing: -.3px;
  }
  .brand__dot {
    width: 14px; height: 14px; border-radius: 50%; background: var(--brand-red);
  }
  .card--front .brand { position: absolute; top: 78px; left: 0; right: 0; justify-content: center; }

  .front__details {
    position: absolute; left: 0; right: 0; top: 175px;
    display: flex; justify-content: center;
  }
  .person { text-align: right; padding-right: 22px; border-right: 1px solid var(--rule-dark); }
  .person__name { color: var(--brand-red); font-weight: 600; font-size: 17px; }
  .person__role { font-size: 14px; margin-bottom: 14px; }
  .person__address { font-size: 14px; line-height: 1.35; }
  .contact { list-style: none; padding-left: 22px; font-size: 13.5px; line-height: 1.55; }
  .contact li { display: flex; align-items: center; gap: 8px; }
  .contact svg { width: 11px; height: 11px; fill: var(--brand-red); flex: none; }

  .card--back .brand { position: absolute; top: 42px; left: 0; right: 0; justify-content: center; }
  .appointment { position: absolute; left: 44px; right: 44px; top: 110px; }
  .appointment__title { text-align: center; font-size: 19px; font-weight: 600; margin-bottom: 22px; }
  .field-row { display: flex; align-items: baseline; gap: 6px; font-size: 14px; margin-bottom: 18px; }
  .field-line { flex: 1; border-bottom: 2px dotted var(--dots); height: 12px; }
  .appointment__notice { font-size: 13.5px; text-align: center; margin-top: 8px; }
</style>
</head>
<body>
<main class="stage">
  <section class="card card--front" aria-label="Business card front">
    <div class="brand"><span class="brand__dot"></span>Brightturn Wellness</div>
    <div class="front__details">
      <div class="person">
        <p class="person__name">Daniel Moore</p>
        <p class="person__role">Managing Director</p>
        <p class="person__address">48, Maple Court Road<br>Eastvale, 402135.</p>
      </div>
      <ul class="contact">
        <li><svg viewBox="0 0 24 24"><path d="M6.6 10.8a15 15 0 0 0 6.6 6.6l2.2-2.2c.3-.3.7-.4 1-.2 1.1.4 2.3.6 3.6.6.6 0 1 .4 1 1V20c0 .6-.4 1-1 1A17 17 0 0 1 3 4c0-.6.4-1 1-1h3.5c.6 0 1 .4 1 1 0 1.3.2 2.5.6 3.6.1.3 0 .7-.2 1z"/></svg>044-987 654 321</li>
        <li><svg viewBox="0 0 24 24"><path d="M2 5h20v14H2z M2 6l10 7 10-7" /></svg>hello@brightturn.com</li>
        <li><svg viewBox="0 0 24 24"><circle cx="12" cy="12" r="10"/></svg>www.brightturn.com</li>
      </ul>
    </div>
  </section>

  <section class="card card--back" aria-label="Appointment card">
    <div class="brand"><span class="brand__dot"></span>Brightturn Wellness</div>
    <div class="appointment">
      <p class="appointment__title">Your Next Appointment is</p>
      <div class="field-row"><span>Name:</span><span class="field-line"></span></div>
      <div class="field-row"><span>Date:</span><span class="field-line"></span><span>Time:</span><span class="field-line"></span></div>
      <p class="appointment__notice">If unable to keep appointment, kindly give 24hrs notice.</p>
    </div>
  </section>
</main>
</body>
</html>
```